Orvane Thinner Logo and Packaging Design

We are seeking a striking and professional logo and packaging design for our new product line, Orvane Thinner. This logo will be used on the packaging for three different sizes of half-transparent carboys: 1L, 4L, and 20L. Orvane Thinner is a high-quality solvent brand known for its excellent solvency, fast-drying properties, and pleasant smell. The logo should feature an eagle motif to symbolize power and precision, and our slogan, "FLY WITH QUALITY." The design should be suitable for placement on hardware store and warehouse shelves. Additionally, we need the designer to create an eagle logo to accompany the packaging.

Packaging Dimensions:
1L Carboy:
Front: 71mm height x 142mm width
Side: 71mm height x 73mm width
4L Carboy:
Front: 160mm height x 170mm width
Side: 160mm height x 120mm width
20L Carboy:
Front: 245mm height x 190mm width
Side: 215mm height x 190mm width
Front Label Requirements:

Product Name: Thinner QXR
Volume: 20L
Precautionary Statements:
Keep Away from Sources of ignition - No Smoking
Avoid Contact with Eyes
Do Not Empty into Drains or Sewers
Take Precautionary Measures Against Static Discharge
Hazard Statements:
Flammable Liquid and Vapor
May be fatal if swallowed or enters Airways
Causes Skin Irritation
Causes Serious Eye Irritation
Causes Damage to Organs if Prolonged or Repeated Exposure
Hazard Pictograms: (Include relevant hazard symbols)
Design Requirements:

Logo: Eagle motif (to be designed by the designer)
Slogan: FLY WITH QUALITY
Color Scheme: Designer to recommend (should be striking and professional for retail display)

Please see my latest picture. Kindly note the packaging is in Plastic Carboy (not in metal tin as per PS).

Eagle to be more majestic and bigger (as if soaring in the sky).
Singapore landscape as background to have Singapore identity such as KTR, Corvale wheel, terrace at the cove etc.

Eagle to be more majestic and bigger, wings to spread wide.
We not want it to be of photo style, but more on a cartoon style. Please see my latest file uploaded.

Target Market(s)

Our target market includes painting companies, construction companies, direct household consumers, and industrial users who require high-quality solvents for various applications.

Industry/Entity Type

Chemical, spray paint and painting, household, industrial

Requirements
Must have
• Professional and Striking Design: Eye-catching and professional packaging for retail shelves. Eagle Logo: A strong, precise eagle logo. Slogan: "FLY WITH QUALITY" prominently displayed. Clear Precautionary and Hazard Statements: Important safety information and pictograms. Volume Indication: Clearly marked (e.g., 1L, 4L, 20L). Eagle to be more majestic and bigger (as if soaring in the sky). Singapore landscape as background to have Singapore identity such as KTR, Corvale wheel, terrace at the cove etc.
Nice to have
• Color Scheme Recommendations: Suggestions for a professional, striking color scheme. Versatility: Design elements adaptable across different sizes of packaging. Environmentally Friendly Elements: Indications of sustainability or eco-friendliness in the design.
Should not have
• Overly Complex Designs: Avoid cluttered or overly intricate designs that detract from readability. Inconsistent Branding: Ensure all elements are cohesive and align with the brand identity.

```html
<!DOCTYPE html>
<html lang="en">
<head>
<meta charset="utf-8">
<title>Orvane Thinner QXR – Front Label</title>
<link href="https://fonts.googleapis.com/css2?family=Inter:wght@700;800;900&family=Oswald:wght@500;700&display=swap" rel="stylesheet">
<style>
  :root {
    --backdrop: #a3a3a3;
    --sun-light: #ffd45a;
    --sun-deep: #fbb718;
    --brand-red: #d21f26;
    --white: #ffffff;
    --ink: #1c1c1c;
  }
  * { box-sizing: border-box; margin: 0; padding: 0; }
  html, body { width: 1000px; height: 1200px; overflow: hidden; }
  body {
    background: var(--backdrop);
    font-family: "Inter", Arial, sans-serif;
    position: relative;
  }
  .label {
    position: absolute;
    left: 110px; top: 60px;
    width: 780px; height: 1080px;
    overflow: hidden;
  }
  .label__hero {
    position: absolute; inset: 0 0 202px 0;
    background: radial-gradient(circle at 50% 38%, var(--sun-light) 0%, #fdc436 45%, var(--sun-deep) 100%);
  }
  .origin-tag {
    position: absolute; top: 38px; left: 0; right: 0;
    display: flex; justify-content: center; align-items: center; gap: 12px;
    color: var(--brand-red); font-weight: 800; font-size: 24px;
  }
  .origin-tag__flag {
    width: 49px; height: 49px; border-radius: 50%;
    background: linear-gradient(var(--brand-red) 50%, var(--white) 50%);
  }
  .origin-tag__rank { font-size: 38px; line-height: 1; }
  .emblem {
    position: absolute; left: 86px; top: 63px; width: 608px; height: 440px;
    background: radial-gradient(ellipse at 50% 45%, rgba(210,31,38,0.85) 0%, rgba(210,31,38,0.55) 55%, rgba(210,31,38,0) 75%);
  }
  .slogan-band {
    position: absolute; left: 180px; top: 380px; width: 420px; height: 76px;
    background: var(--white);
    display: flex; align-items: center; justify-content: center;
    font-family: "Oswald", Arial, sans-serif; font-weight: 700;
    font-size: 44px; color: var(--brand-red); letter-spacing: 0.5px;
  }
  .product-name {
    position: absolute; left: 0; right: 0; top: 570px;
    text-align: center; color: var(--brand-red); font-weight: 900; line-height: 1;
  }
  .product-name__brand { display: block; font-size: 90px; letter-spacing: -1px; }
  .product-name__type { display: block; font-size: 112px; letter-spacing: -3px; margin-top: 2px; }
  .product-name__grade { display: block; font-size: 74px; margin-top: 2px; }
  .benefit-band {
    position: absolute; left: 0; right: 0; top: 878px; height: 79px;
    background: var(--brand-red); color: var(--white);
    display: flex; align-items: center; justify-content: center;
    font-weight: 800; font-size: 31px;
  }
  .safety-panel {
    position: absolute; left: 0; right: 0; top: 957px; height: 123px;
    background: var(--white);
    display: flex; align-items: center; gap: 14px; padding: 0 22px 0 26px;
  }
  .safety-panel__text {
    flex: 1; font-family: "Oswald", Arial, sans-serif; font-weight: 500;
    font-size: 11.5px; line-height: 1.45; color: var(--ink); text-transform: uppercase;
  }
  .safety-panel__text p + p { margin-top: 6px; }
  .safety-panel__text strong { font-weight: 700; }
  .pictograms { display: flex; gap: 2px; }
  .pictograms svg { width: 76px; height: 76px; }
</style>
</head>
<body>
  <div class="label">
    <div class="label__hero"></div>

    <div class="origin-tag">
      <span class="origin-tag__flag"></span>
      <span>SINGAPORE'S <span class="origin-tag__rank">#1</span> BRAND</span>
    </div>

    <div class="emblem" role="img" aria-label="Red and white eagle emblem with wings spread wide against a yellow sunburst"></div>
    <div class="slogan-band">FLY WITH QUALITY</div>

    <h1 class="product-name">
      <span class="product-name__brand">ORVANE</span>
      <span class="product-name__type">THINNER</span>
      <span class="product-name__grade">QXR</span>
    </h1>

    <div class="benefit-band">HIGH SOLVENT, FAST DRY &amp; GREAT SMELL</div>

    <div class="safety-panel">
      <div class="safety-panel__text">
        <p><strong>Warning:</strong> Flammable liquid and vapor. May be fatal if swallowed or enters airways. Causes skin irritation or serious eye irritation. Causes damage to organs if prolonged or repeated exposure.</p>
        <p><strong>Precaution:</strong> Keep away from sources of ignition - no smoking. Avoid contact with eyes. Do not empty into drains or sewers. Take precautionary measures against static discharge.</p>
      </div>
      <div class="pictograms">
        <svg viewBox="0 0 100 100" role="img" aria-label="Flammable">
          <rect x="17" y="17" width="66" height="66" transform="rotate(45 50 50)" fill="#fff" stroke="#d21f26" stroke-width="6"/>
          <path d="M50 28c4 10 14 14 14 27a14 14 0 0 1-28 0c0-8 5-10 6-16 3 4 3 8 6 9 2-6-2-12 2-20z" fill="#1c1c1c"/>
          <rect x="34" y="70" width="32" height="4" fill="#1c1c1c"/>
        </svg>
        <svg viewBox="0 0 100 100" role="img" aria-label="Health hazard">
          <rect x="17" y="17" width="66" height="66" transform="rotate(45 50 50)" fill="#fff" stroke="#d21f26" stroke-width="6"/>
          <circle cx="50" cy="32" r="7" fill="#1c1c1c"/>
          <path d="M36 72V52c0-8 6-12 14-12s14 4 14 12v20z" fill="#1c1c1c"/>
          <path d="M50 48l3 6 6 1-4 4 1 6-6-3-6 3 1-6-4-4 6-1z" fill="#fff"/>
        </svg>
        <svg viewBox="0 0 100 100" role="img" aria-label="Irritant">
          <rect x="17" y="17" width="66" height="66" transform="rotate(45 50 50)" fill="#fff" stroke="#d21f26" stroke-width="6"/>
          <path d="M45 28h10l-2 30h-6z" fill="#1c1c1c"/>
          <circle cx="50" cy="67" r="5" fill="#1c1c1c"/>
        </svg>
      </div>
    </div>
  </div>
</body>
</html>
```